Fernwick Landscaping Folder Design

I need a graphic designer to design a folder so we can insert informational sheets inside it for customers. The folder must include the company logo, project images, on front and back of folder and slogan " The Experience You Want, The Service You Expect, And The Value You Deserve'

Folder to also include phone numbers : 416 555 0193 as well as the website: www.fernwicklandscaping.example as well as we gurantee a 24 month warranty.

I have attached sample of size we need.

Pixel Harbor has also done something similar for me for Tollbridge Landscapes

Target Market(s)

geared toward home owners & commercial/industrial

Industry/Entity Type

Landscaping

Font styles to use
Other font styles liked:
• open to new trendy font

Requirements
Must have
• Telephone Number, email address, slogan, images,
Nice to have
• images of completed projects incorporated into the front and back of folder as well as the logo
Should not have
• n/a

```html
<!DOCTYPE html>
<html lang="en">
<head>
<meta charset="utf-8">
<title>Fernwick Landscaping Folder</title>
<link rel="stylesheet" href="https://fonts.googleapis.com/css2?family=Oswald:wght@300;600&family=Open+Sans:wght@600;700&display=swap">
<style>
  :root {
    --stage: #e9ebec;
    --paper: #ffffff;
    --mist: #dcecef;
    --mist-deep: #c4dde3;
    --slogan: #cdd2d5;
    --ink: #3a3a3a;
    --brand-green: #4fae2c;
    --muted: #6b6f72;
  }
  * { box-sizing: border-box; margin: 0; padding: 0; }
  html, body { width: 1200px; height: 848px; overflow: hidden; background: var(--stage); }
  .canvas { position: relative; width: 1200px; height: 848px; }

  .folder-panel {
    position: absolute; top: 124px; width: 420px; height: 600px;
    background: var(--paper); overflow: hidden;
    box-shadow: 0 6px 18px rgba(0,0,0,.18);
  }
  .folder-front { left: 150px; }
  .folder-back  { left: 630px; }
  .panel-art { position: absolute; inset: 0; width: 420px; height: 600px; }

  .brand-mark {
    position: absolute; top: 130px; left: 0; width: 100%;
    display: flex; justify-content: center; align-items: center; gap: 10px;
    font-family: "Oswald", sans-serif; font-weight: 600;
    font-size: 26px; letter-spacing: 1px; text-transform: uppercase; color: var(--ink);
  }
  .brand-square { width: 14px; height: 14px; background: var(--ink); }

  .slogan {
    position: absolute; top: 200px; left: 120px;
    font-family: "Oswald", sans-serif; text-transform: uppercase;
    color: var(--slogan); font-size: 27px; line-height: 30px;
  }
  .slogan .soft { font-weight: 300; display: block; }
  .slogan .strong { font-weight: 600; display: block; }

  .warranty {
    position: absolute; top: 448px; left: 40px; width: 340px;
    font-family: "Open Sans", sans-serif; font-weight: 700;
    color: var(--brand-green); font-size: 17px; text-transform: uppercase;
    padding-bottom: 8px; border-bottom: 1px solid var(--brand-green);
  }
  .contact-line {
    position: absolute; top: 486px; left: 40px;
    display: flex; align-items: center; gap: 6px;
    font-family: "Open Sans", sans-serif; font-weight: 600;
    font-size: 12px; color: var(--brand-green);
  }
  .contact-icon { width: 13px; height: 13px; }
  .contact-gap { width: 10px; }
</style>
</head>
<body>
<main class="canvas">

  <section class="folder-panel folder-front">
    <svg class="panel-art" viewBox="0 0 420 600" aria-hidden="false">
      <defs>
        <linearGradient id="mistFade" x1="0" y1="0" x2="1" y2="1">
          <stop offset="0" stop-color="var(--mist-deep)" stop-opacity=".7"/>
          <stop offset=".6" stop-color="var(--mist)" stop-opacity=".25"/>
          <stop offset="1" stop-color="#ffffff" stop-opacity="0"/>
        </linearGradient>
        <linearGradient id="driveTone" x1="1" y1="0" x2="0" y2="1">
          <stop offset="0" stop-color="#6f7a5a"/>
          <stop offset=".45" stop-color="#9ea59a"/>
          <stop offset="1" stop-color="#ffffff"/>
        </linearGradient>
      </defs>
      <path d="M0,0 H420 V140 Q250,40 0,120 Z" fill="url(#mistFade)"/>
      <path d="M60,0 Q260,90 420,60 V0 Z" fill="var(--mist)" opacity=".5"/>
      <path d="M0,600 V470 Q200,390 420,330 V600 Z" fill="url(#driveTone)"
            role="img" aria-label="Photo of a finished curved concrete driveway in front of a house with autumn trees"/>
      <path d="M0,470 Q200,390 420,330" fill="none" stroke="#ffffff" stroke-width="3"/>
    </svg>
    <div class="brand-mark"><span class="brand-square"></span>Fernwick Landscaping</div>
    <p class="slogan">
      <span class="soft">The Experience</span>
      <span class="strong">You Want,</span>
      <span class="soft">The Service</span>
      <span class="strong">You Expect,</span>
      <span class="soft">And The Value</span>
      <span class="strong">You Deserve</span>
    </p>
  </section>

  <section class="folder-panel folder-back">
    <svg class="panel-art" viewBox="0 0 420 600">
      <defs>
        <linearGradient id="pocketMist" x1="0" y1="0" x2="0" y2="1">
          <stop offset="0" stop-color="var(--mist)"/>
          <stop offset=".5" stop-color="#ffffff"/>
        </linearGradient>
      </defs>
      <rect x="0" y="0" width="420" height="140" fill="#8d9488" role="img" aria-label="Photo of a stone patio with steps and garden beds"/>
      <rect x="200" y="90" width="220" height="160" fill="#c9c3b6" role="img" aria-label="Photo of a stone driveway leading to a white garage"/>
      <rect x="0" y="140" width="200" height="120" fill="#3f6fa8" role="img" aria-label="Photo of a lit backyard pool at dusk"/>
      <rect x="0" y="250" width="420" height="160" fill="#8e9399" role="img" aria-label="Photo of a commercial paving site with parked vehicles"/>
      <path d="M0,370 Q120,360 215,400 Q310,340 420,330 V600 H0 Z" fill="url(#pocketMist)"/>
      <path d="M0,370 Q120,360 215,400 Q310,340 420,330" fill="none" stroke="#ffffff" stroke-width="3"/>
    </svg>
    <p class="warranty">We gurantee a 24 month warranty</p>
    <p class="contact-line">
      <svg class="contact-icon" viewBox="0 0 16 16"><circle cx="8" cy="8" r="8" fill="var(--muted)"/><path d="M5 4h2l1 2-1 1a5 5 0 0 0 2 2l1-1 2 1v2a1 1 0 0 1-1 1A7 7 0 0 1 4 5a1 1 0 0 1 1-1z" fill="#fff"/></svg>
      <span>416 555 0193</span>
      <span class="contact-gap"></span>
      <svg class="contact-icon" viewBox="0 0 16 16"><circle cx="8" cy="8" r="8" fill="var(--muted)"/><circle cx="8" cy="8" r="4.5" fill="none" stroke="#fff"/><path d="M3.5 8h9M8 3.5v9" stroke="#fff"/></svg>
      <span>www.fernwicklandscaping.example</span>
    </p>
  </section>

</main>
</body>
</html>
```